Hearthside Lending Relief

Please help us give our website a remake or a FACELIFT. It is not very good but it says what we need it to say. But the design is terrible.
I would like our new design font and logo to be used as the theme.

I also want more photos on the site.

I also want consistency with the pages so they look clean.

We want the professionals to do this, let's see what you got!

Thank you!
Updates

Project Deadline Extended
Reason: I can understand you want to be paid. So I will commit to the fee but I want you to have time to make a KICK ASS website for me dudes! Thanks

HI!  Just wanted to say thanks for your time on these.  A lot are great.  However the firefighters have nothing to do with Foreclosure.  We are saving peoples homes from the bank taking them and selling them.   I LOVE the house photos and the families on the website.  That is the direction we like.  THanks.

THANK U ALL FOR THE WORK!   I like a few ending in the numbers: 147  733  693  536  620  478  727  508     I will go over them and choose one soon.  Thank you.   You will be paid shortly. 

Requirements
Must have
• Bright, Upbeat photos. Color scheme should be in order. We like icons on the bottom. not just text.

```html
<!DOCTYPE html>
<html lang="en">
<head>
<meta charset="utf-8">
<title>Hearthside Lending Relief</title>
<link rel="stylesheet" href="https://fonts.googleapis.com/css2?family=Arimo:wght@400;700&display=swap">
<style>
:root{
  --red:#e53e30;
  --red-deep:#b82a20;
  --ink:#1c1c1c;
  --white:#ffffff;
  --band:rgba(30,30,30,.62);
  --sky:#8fb0cf;
  --brick:#a08a72;
  --shadow-ink:#2e2824;
}
*{margin:0;padding:0;box-sizing:border-box}
html,body{width:1200px;height:1050px;overflow:hidden;background:var(--white)}
body{font-family:"Arimo",Arial,sans-serif;color:var(--ink);position:relative}

.hero-photo{position:absolute;left:0;top:0;width:1200px;height:470px;
  background:
    radial-gradient(ellipse 260px 300px at 830px 300px,rgba(60,50,44,.85),rgba(60,50,44,0) 100%),
    radial-gradient(ellipse 380px 220px at 380px 330px,rgba(150,128,104,.95),rgba(150,128,104,0) 100%),
    linear-gradient(180deg,#6f98c2 0%,#a9c1d8 38%,#c9d5df 55%,#8b7b68 78%,#3a332d 100%)}

.nav{position:absolute;top:0;height:37px;background:var(--red);display:flex;align-items:center;
  font-weight:700;font-size:12.5px;color:var(--white);z-index:3}
.nav a{color:inherit;text-decoration:none}
.nav-left{left:106px;width:326px;border-bottom-left-radius:12px;clip-path:polygon(0 0,100% 0,100% 100%,2% 100%);padding-left:59px;gap:34px}
.nav-right{left:746px;width:346px;border-bottom-right-radius:12px;clip-path:polygon(0 0,100% 0,98% 100%,0 100%);padding-left:52px;gap:24px}

.brand-panel{position:absolute;left:432px;top:0;width:314px;height:172px;z-index:3}
.brand-panel svg{position:absolute;inset:0}
.brand{position:absolute;left:22px;top:36px;display:flex;align-items:center;gap:12px}
.brand-mark{width:80px;height:80px;border-radius:50%;background:var(--red);flex:none}
.brand-name{color:var(--red);font-weight:700;font-size:20px;line-height:21px;text-transform:uppercase}

.call{position:absolute;right:132px;top:45px;text-align:right;z-index:3}
.call-label{color:var(--red);font-weight:700;font-size:19px;display:flex;align-items:center;justify-content:flex-end;gap:2px}
.call-number{font-weight:700;font-size:20px;color:#111;margin-top:1px}

.tagline-band{position:absolute;left:0;top:385px;width:1200px;height:62px;background:var(--band)}
.tagline{position:absolute;top:396px;left:0;width:1132px;text-align:center;color:var(--white);font-weight:700;font-size:15.5px;line-height:19px;word-spacing:5px}

.sidebar{position:absolute;left:108px;top:460px;width:248px;height:438px;
  background:linear-gradient(90deg,#fff 0%,#f3f3f3 80%,#d8d8d8 100%)}
.hero-curve{position:absolute;left:0;top:436px;z-index:2}

.side-photo{position:absolute;border:2px solid var(--red);border-radius:8px;box-shadow:0 6px 8px rgba(0,0,0,.14)}
.side-photo.one{left:128px;top:516px;width:215px;height:141px;
  background:linear-gradient(120deg,#eef0f2 0%,#d9d1bd 35%,#8b8478 55%,#c8b98a 75%,#e7d58f 100%)}
.side-photo.two{left:124px;top:707px;width:217px;height:141px;
  background:linear-gradient(180deg,#c9d6e2 0%,#b59a88 40%,#6e5652 70%,#2e2a2a 100%)}

.copy{font-size:12px;line-height:18px;color:#222;letter-spacing:-0.25px}
.welcome{position:absolute;left:371px;top:497px;width:707px}
.welcome h1{color:var(--red);font-size:20px;font-weight:700;padding-bottom:3px;border-bottom:1px solid var(--red);padding-left:2px}
.copy.intro{margin-top:5px}
.copy.more{position:absolute;left:376px;top:697px;width:706px}
.copy.more p+p{margin-top:18px}

.footer{position:absolute;left:0;top:898px;width:1200px;height:127px;
  background:linear-gradient(90deg,var(--red) 0%,#e04434 55%,var(--red-deep) 100%);color:var(--white);font-size:12px;line-height:18px}
.footer-es{position:absolute;left:121px;top:14px;width:247px;text-align:justify;text-align-last:justify}
.footer-es span{display:block}
.footer-es .short{text-align-last:left}
.footer-address{position:absolute;right:134px;top:28px;text-align:right;font-style:normal}
.footer-address strong{font-weight:700}

.bottom-bar{position:absolute;left:0;top:1025px;width:1200px;height:25px;background:#000;color:var(--white);font-size:12px;display:flex;align-items:center}
.bottom-bar nav{margin-left:118px;display:flex;gap:32px}
.bottom-bar a{color:inherit;text-decoration:none}
.copyright{position:absolute;right:109px}
</style>
</head>
<body>
<div class="hero-photo" role="img" aria-label="Smiling family of three standing in front of their two-storey brick house at dusk"></div>

<nav class="nav nav-left"><a href="#">Home</a><a href="#">About Us</a><a href="#">Services</a></nav>
<nav class="nav nav-right"><a href="#">Financing Options</a><a href="#">Query</a><a href="#">Contact Us</a></nav>

<div class="brand-panel">
  <svg width="314" height="172" viewBox="0 0 314 172">
    <defs><linearGradient id="panelShade" x1="0" y1="0" x2="0" y2="1"><stop offset="0" stop-color="#ffffff"/><stop offset="1" stop-color="#e6e6e6"/></linearGradient></defs>
    <path d="M0 0H314V142L157 172L0 142Z" fill="url(#panelShade)"/>
  </svg>
  <div class="brand">
    <span class="brand-mark"></span>
    <span class="brand-name">Hearthside<br>Lending<br>Relief</span>
  </div>
</div>

<div class="call">
  <div class="call-label">
    <svg width="14" height="20" viewBox="0 0 14 20"><path d="M3 1c2 0 3 4 2 5L4 7c0 3 2 6 4 7l1-1c1-1 4 1 4 3s-2 3-3 3C5 19 1 12 1 5c0-2 1-4 2-4z" fill="none" stroke="#e53e30" stroke-width="2"/></svg>
    Call Us
  </div>
  <div class="call-number">888-555-0142</div>
</div>

<div class="tagline-band"></div>
<p class="tagline">Offering&nbsp; solid alternatives<br>to losing your home in a Trustee Sale</p>

<div class="sidebar"></div>
<svg class="hero-curve" width="1200" height="36" viewBox="0 0 1200 36">
  <path d="M0 16C300 4 800 0 1200 6V36H0Z" fill="#e53e30"/>
  <path d="M0 33C320 18 800 14 1200 24V36H0Z" fill="#ffffff"/>
</svg>

<div class="side-photo one" role="img" aria-label="Couple embracing as they look at a modern house"></div>
<div class="side-photo two" role="img" aria-label="Happy extended family posing together outdoors"></div>

<section class="welcome">
  <h1>Welcome to Hearthside Lending Relief</h1>
  <p class="copy intro">HEARTHSIDE LENDING RELIEF specializes in assisting homeowners who are in FORECLOSURE, by offering solid alterna-tives to losing your home in a Trustee Sale.&nbsp; Having your home foreclosed on can damage your credit for up to 7 years.&nbsp; Most foreclosures end with the home owner being evicted from their home, leaving them with no money, no place to live and without ample time to safely remove their possessions from their home.&nbsp; There is no need to have this happen to you.&nbsp; No matter what part of foreclosure process you are in, WE CAN HELP!<br>If you have received a Notice of Default (NOD) or Notice of Trustee Sale (NTS), you have options.&nbsp; Contact us today to speak to one of our licensed specialist, and let us help you put this situation behind you.</p>
</section>

<div class="copy more">
  <p>We speak to hundreds of homeowners every day, we understand how frustrating this can be.&nbsp; Don't live in fear of what is to come. You have other options, please call or email us today and we will immediately put our specialist to work finding you a solution.</p>
  <p>Don't try to handle this frustrating situation by yourself.&nbsp; HEARTHSIDE LENDING RELIEF is a team of knowledgeable real estate professionals, we can offer you a better solution during this tough time.</p>
  <p>HEARTHSIDE LENDING RELIEF has been assisting families in foreclosure for years.&nbsp; Our skill and integrity has earned us a reputation for fast, professional, courteous and thorough solutions.&nbsp; With over 50 years of real estate knowledge and experience HEARTHSIDE LENDING RELIEF is ready to assist you.</p>
</div>

<footer class="footer">
  <p class="footer-es">
    <span class="short">Si el banco esta a punto de subastar su casa!</span>
    <span>No se den por vencidos. Estamos aqui para</span>
    <span class="short">proveerles opciones.</span>
    <span>Hablenos al numero 888-555-0142 para una</span>
    <span>consulta gratuita. Hablamos Espanol.</span>
  </p>
  <address class="footer-address">
    <strong>HEARTHSIDE LENDING RELIEF</strong><br>
    218 Harbor View Avenue, Suite 300<br>
    Oceanside, CA 92054<br>
    Call us : 888-555-0142
  </address>
</footer>

<div class="bottom-bar">
  <nav><a href="#">Home</a><a href="#">About Us</a><a href="#">Services</a><a href="#">Financing Options</a><a href="#">Contact Us</a></nav>
  <span class="copyright">Content copyright 2012. HEARTHSIDELENDINGRELIEF.COM. All rights reserved.</span>
</div>
</body>
</html>
```